Lawn care business card

I am looking for a quality designed personal business card to represent the quality and elegant nature of our company. We separate ourselves in our market by the aesthetic value of our work, so I am looking for marketing material that does the same. We target our marketing high end customers, and we try to avoid price shoppers. I am open to all design options, so long as they are in line with our companies values.

We are tend to go with a retro look on everything from our logo and print material, to our uniforms. We like to portray and "old fashion" set of core values, with a modern elegance. So a wild and crazy look is out of the question.

Things I'd like on the card:
1.) Logo
2.) Phone number: (816) 555-2931
3.) Website: Verdelynkc.com
4.) Email: robertfairley@verdelynkc.com
5.) My name: Robert Fairley
6.) Facebook link: facebook.com/VerdelynGardenandGrounds
7.) Instagram: http://instagram.com/verdelynkc

Attached is a copy of our logo.

Reason: More time is needed to gather conclusive feedback from the members of our marketing team.

```html
<!DOCTYPE html>
<html lang="en">
<head>
<meta charset="utf-8">
<title>Verdelyn Garden &amp; Grounds – Business Card</title>
<link href="https://fonts.googleapis.com/css2?family=Lato:wght@300;400;700;900&display=swap" rel="stylesheet">
<style>
  :root {
    --page: #ece9e4;
    --card: #ffffff;
    --ink: #2a2a2a;
    --band: #2e2e2e;
    --band-text: #ffffff;
    --accent: #f07a2a;
    --muted: #3a3a3a;
  }
  html, body {
    margin: 0;
    padding: 0;
    width: 1200px;
    height: 1023px;
    overflow: hidden;
    background: var(--page);
    font-family: "Lato", Arial, sans-serif;
  }
  .canvas {
    position: relative;
    width: 1200px;
    height: 1023px;
  }
  .card {
    position: absolute;
    left: 380px;
    top: 116px;
    width: 440px;
    height: 790px;
    background: var(--card);
    box-shadow: 0 10px 30px rgba(0,0,0,.18);
  }
  .brand {
    position: absolute;
    top: 0;
    left: 0;
    right: 0;
    height: 330px;
    display: flex;
    align-items: center;
    justify-content: center;
    gap: 16px;
  }
  .brand-dot {
    width: 30px;
    height: 30px;
    border-radius: 50%;
    background: var(--accent);
  }
  .brand-name {
    font-weight: 900;
    font-size: 50px;
    letter-spacing: 3px;
    color: var(--ink);
    text-transform: uppercase;
  }
  .name-band {
    position: absolute;
    top: 330px;
    left: 0;
    right: 0;
    height: 96px;
    background: var(--band);
    color: var(--band-text);
    display: flex;
    flex-direction: column;
    align-items: center;
    justify-content: center;
  }
  .person {
    font-size: 30px;
    font-weight: 300;
    letter-spacing: .5px;
  }
  .person strong { font-weight: 700; }
  .role {
    margin-top: 4px;
    font-size: 15px;
    font-weight: 700;
    letter-spacing: 1px;
  }
  .website {
    position: absolute;
    top: 462px;
    left: 0;
    right: 0;
    text-align: center;
    color: var(--accent);
    font-size: 24px;
    font-weight: 700;
    letter-spacing: 4px;
  }
  .contacts {
    position: absolute;
    top: 530px;
    left: 46px;
    right: 30px;
    margin: 0;
    padding: 0;
    list-style: none;
  }
  .contact {
    display: flex;
    align-items: center;
    gap: 14px;
    height: 44px;
    font-size: 16px;
    color: var(--muted);
    white-space: nowrap;
  }
  .contact-icon {
    flex: none;
    width: 24px;
    height: 24px;
  }
  .contact-icon--blank {
    width: 24px;
    height: 24px;
    border-radius: 50%;
    background: var(--accent);
    flex: none;
  }
</style>
</head>
<body>
<main class="canvas">
  <section class="card" aria-label="Business card front">
    <header class="brand">
      <span class="brand-dot"></span>
      <span class="brand-name">Verdelyn</span>
    </header>

    <div class="name-band">
      <div class="person">Robert <strong>Fairley</strong></div>
      <div class="role">OWNER / FOUNDER</div>
    </div>

    <div class="website">www.Verdelynkc.com</div>

    <ul class="contacts">
      <li class="contact">
        <svg class="contact-icon" viewBox="0 0 24 24" aria-hidden="true">
          <circle cx="12" cy="12" r="12" fill="var(--accent)"/>
          <path d="M8.2 6.5c.4-.3 1-.3 1.3.1l1.3 1.8c.3.4.2.9-.1 1.2l-.8.7c.6 1.3 1.6 2.3 2.9 2.9l.7-.8c.3-.3.8-.4 1.2-.1l1.8 1.3c.4.3.4.9.1 1.3l-.9 1c-.5.5-1.3.7-2 .4-3-1.2-5.3-3.5-6.5-6.5-.3-.7-.1-1.5.4-2z" fill="#fff"/>
        </svg>
        (816) 555-2931
      </li>
      <li class="contact">
        <svg class="contact-icon" viewBox="0 0 24 24" aria-hidden="true">
          <circle cx="12" cy="12" r="12" fill="var(--accent)"/>
          <rect x="6" y="8" width="12" height="8.5" rx="1" fill="#fff"/>
          <path d="M6.5 8.6l5.5 4.2 5.5-4.2" fill="none" stroke="var(--accent)" stroke-width="1.2"/>
        </svg>
        robertfairley@verdelynkc.com
      </li>
      <li class="contact">
        <span class="contact-icon--blank"></span>
        picsfeed.com/verdelynkc
      </li>
      <li class="contact">
        <span class="contact-icon--blank"></span>
        socialpage.com/VerdelynGardenandGrounds
      </li>
    </ul>
  </section>
</main>
</body>
</html>
```